Roofing company in Toronto, Canada needs a logo design and business card design

We need a business card and logo created for our company. Our company is "KLV Roofing" which provides roofing services for commercial and residential customers. We serve customers in the Greater Toronto Area (in Canada) thus the name KLV.

We want the logo and business card to be a modern design displaying professionalism and quality in the work. We would prefer rounded corners for the business cards but are open to other ideas. The cards should be pleasant and appealing to customers.

Target Market(s)

Commercial and Residential customers

Industry/Entity Type

Roofing

Contact Information for Business Card

Logo Text

KLV Roofing

Requirements
Nice to have
• Colours that are pleasing to the eye but at the same time should stand out from other business cards. If the design can incorporate the name of KLV Roofing and the actual concept of roofing that would be nice.
Should not have
• Do not want the business cards or logo to be childish looking. Need to look professionally designed.

```html
<!DOCTYPE html>
<html lang="en">
<head>
<meta charset="utf-8">
<title>KLV Roofing – Business Card</title>
<link rel="stylesheet" href="https://fonts.googleapis.com/css2?family=Lato:wght@400;700&display=swap">
<style>
  :root {
    --page-bg: #e9e6e4;
    --card-light: #f4f1f0;
    --brand-red: #b50000;
    --brand-grey: #7b7b7b;
    --text-on-red: #ffffff;
  }
  * { margin: 0; padding: 0; box-sizing: border-box; }
  html, body {
    width: 1200px; height: 900px; overflow: hidden;
    background: var(--page-bg);
    font-family: "Lato", Arial, sans-serif;
  }
  .business-card {
    position: absolute; left: 162px; top: 180px;
    width: 876px; height: 540px;
    display: flex;
    box-shadow: 0 10px 30px rgba(0,0,0,0.15);
  }
  .card-front {
    width: 465px; height: 100%;
    background: var(--card-light);
    display: flex; align-items: center; justify-content: center;
  }
  .brand-name {
    display: flex; align-items: center; gap: 16px;
    color: var(--brand-red);
    font-weight: 700; font-size: 62px; letter-spacing: 1px;
  }
  .brand-mark {
    width: 22px; height: 22px; background: var(--brand-red);
  }
  .card-details {
    position: relative;
    width: 411px; height: 100%;
    background: var(--brand-red);
    color: var(--text-on-red);
  }
  .person-name {
    position: absolute; left: 35px; top: 84px;
    font-size: 31px; font-weight: 700;
  }
  .person-title {
    position: absolute; left: 35px; top: 122px;
    font-size: 24px; font-weight: 400;
  }
  .contact-list { list-style: none; position: absolute; left: 35px; top: 186px; }
  .contact-list li {
    display: flex; align-items: center; gap: 10px;
    height: 36px; font-size: 24px;
  }
  .contact-icon { width: 20px; height: 20px; fill: var(--text-on-red); flex: none; }
  .address {
    position: absolute; left: 35px; top: 358px;
    font-size: 24px; line-height: 31px; font-style: normal;
  }
</style>
</head>
<body>
  <div class="business-card">
    <div class="card-front">
      <div class="brand-name"><span class="brand-mark"></span>KLV Roofing</div>
    </div>
    <div class="card-details">
      <div class="person-name">Daniel Mercer</div>
      <div class="person-title">Managing Director</div>
      <ul class="contact-list">
        <li>
          <svg class="contact-icon" viewBox="0 0 24 24"><path d="M6.6 10.8a15.2 15.2 0 0 0 6.6 6.6l2.2-2.2a1 1 0 0 1 1-.25 11.4 11.4 0 0 0 3.6.57 1 1 0 0 1 1 1V20a1 1 0 0 1-1 1A17 17 0 0 1 3 4a1 1 0 0 1 1-1h3.5a1 1 0 0 1 1 1c0 1.25.2 2.45.57 3.57a1 1 0 0 1-.25 1z"/></svg>
          416-555-0142
        </li>
        <li>
          <svg class="contact-icon" viewBox="0 0 24 24"><path d="M7 1h10a2 2 0 0 1 2 2v18a2 2 0 0 1-2 2H7a2 2 0 0 1-2-2V3a2 2 0 0 1 2-2zm0 3v14h10V4zm5 15.5a1.2 1.2 0 1 0 0 2.4 1.2 1.2 0 0 0 0-2.4z"/></svg>
          416-555-0142
        </li>
        <li>
          <svg class="contact-icon" viewBox="0 0 24 24"><path d="M2 5h20v14H2zm2 2v.5l8 5 8-5V7zm0 2.8V17h16V9.8l-8 5z"/></svg>
          info@klvroofing.ca
        </li>
        <li>
          <svg class="contact-icon" viewBox="0 0 24 24"><circle cx="12" cy="12" r="9"/><path d="M3 12h18M12 3c3 3 3 15 0 18M12 3c-3 3-3 15 0 18" stroke="#b50000" stroke-width="1.5" fill="none"/></svg>
          www.klvroofing.ca
        </li>
      </ul>
      <address class="address">
        Addres Line Comes Here,<br>
        Location Pincode 45215<br>
        Country Etc.
      </address>
    </div>
  </div>
</body>
</html>
```